Business Cards Design for the electrical wholesaler: clean bold dynamic :)

We need a business card design that would follow our latest brand guidelines. As an electrical wholesaler we want to bring a fresh look and feel into the industry. The design should be clean bold and dynamic. It should come alive with the renewed energy of our green colour. Our grey colour should keep things balanced and complement the notion of maturity and responsibility. We employ Lato as a corporate font however are not bound by this font and we’re open to interpretation here.

Target Market(s)

Electrical contractors

Industry/Entity Type

Business

Contact Information for Business Card

Logo
Name & Surname: Halyna Dorosh
Job Title: Director of Marketing
Email: halya.dorosh@quillmail.example
Cell phone: XXX.XXX.XXXX
Address: 20517 - 87 Ave. Edmonton, AB, Canada. T6K 4N8
Business Phone: 780.555.0184
Website: www.brovix.example

Font styles to use
Other font styles liked:
• Lato

Requirements
Must have
• Logo & website
Nice to have
• Brand elements - some of them you may find in the attached Brand Guidelines (e.g. three lines on the background signifying "W")

```html
<!DOCTYPE html>
<html lang="en">
<head>
<meta charset="utf-8">
<title>Brovix business card</title>
<link rel="stylesheet" href="https://fonts.googleapis.com/css2?family=Work+Sans:wght@400;500&display=swap">
<style>
  :root {
    --green: #8dc641;
    --grey: #4f4f52;
    --white: #ffffff;
    --faint: #f6f6f6;
    --backdrop: #1f1f1f;
  }
  * { margin: 0; padding: 0; box-sizing: border-box; }
  html, body { width: 1200px; height: 897px; overflow: hidden; }
  body {
    background: var(--backdrop);
    font-family: "Work Sans", sans-serif;
    position: relative;
  }
  .card {
    position: absolute;
    left: 303px;
    width: 594px;
    height: 338px;
    border-radius: 19px;
    overflow: hidden;
  }
  .card-front { top: 92px; background: var(--white); }
  .card-back { top: 469px; background: var(--green); }

  .front-glow {
    position: absolute;
    right: -70px; top: -150px;
    width: 380px; height: 380px;
    border-radius: 50%;
    background: var(--faint);
  }
  .wordmark {
    position: absolute;
    display: flex;
    align-items: center;
    gap: 10px;
    font-weight: 500;
    letter-spacing: -0.5px;
  }
  .wordmark-front { left: 30px; top: 38px; font-size: 46px; color: var(--grey); }
  .wordmark-front .mark-square { width: 30px; height: 30px; background: var(--green); border-radius: 4px; }

  .person { position: absolute; right: 34px; top: 34px; text-align: right; }
  .person-name { font-size: 24px; font-weight: 500; color: var(--green); line-height: 1.2; }
  .person-title { font-size: 16px; color: var(--grey); letter-spacing: 0.5px; }
  .edge-tab {
    position: absolute; right: 0; top: 40px;
    width: 11px; height: 38px;
    background: var(--green);
    border-radius: 5px 0 0 5px;
  }

  .contact-band {
    position: absolute; left: 0; top: 200px;
    width: 400px; height: 114px;
    background: var(--green);
  }
  .contact-list {
    position: absolute; left: 30px; top: 210px;
    list-style: none;
    color: var(--white);
    font-size: 14.5px;
    letter-spacing: 0.4px;
  }
  .contact-list li { display: flex; align-items: center; height: 19px; }
  .contact-list svg { width: 10px; height: 10px; margin-right: 11px; fill: none; stroke: var(--white); stroke-width: 1.4; }
  .address {
    position: absolute; left: 30px; top: 271px;
    color: var(--white);
    font-size: 14.5px;
    line-height: 17px;
    letter-spacing: 0.4px;
  }
  .band-emblem {
    position: absolute; left: 318px; top: 165px;
    width: 210px; height: 210px;
    border-radius: 50%;
    background: var(--grey);
    border: 10px solid var(--white);
  }

  .wordmark-back {
    left: 50%; top: 128px;
    transform: translateX(-50%);
    font-size: 74px;
    color: var(--white);
  }
  .wordmark-back .mark-square { width: 44px; height: 44px; background: var(--white); border-radius: 6px; }
  .back-url {
    position: absolute; left: 0; right: 0; top: 296px;
    text-align: center;
    color: var(--white);
    font-size: 15px;
    letter-spacing: 0.6px;
  }
</style>
</head>
<body>
  <section class="card card-front">
    <div class="front-glow"></div>
    <div class="wordmark wordmark-front"><span class="mark-square"></span>brovix</div>
    <div class="person">
      <p class="person-name">Halyna Dorosh</p>
      <p class="person-title">Founder</p>
    </div>
    <div class="edge-tab"></div>
    <div class="contact-band"></div>
    <ul class="contact-list">
      <li><svg viewBox="0 0 10 10"><path d="M2 1 L4 1 L4.5 3 L3.3 3.8 Q4.5 6 6.2 6.7 L7 5.5 L9 6 L9 8 Q5 9 1.5 4.5 Q1 2.5 2 1Z"/></svg>780.555.0184</li>
      <li><svg viewBox="0 0 10 10"><rect x="1" y="2" width="8" height="6"/><path d="M1 2 L5 5.5 L9 2"/></svg>hello@brovix.example</li>
      <li><svg viewBox="0 0 10 10"><circle cx="5" cy="5" r="4"/><path d="M1 5 H9 M5 1 Q2.5 5 5 9 M5 1 Q7.5 5 5 9"/></svg>www.brovix.example</li>
    </ul>
    <p class="address">20517 87ave<br>T6K4N8 Edmonton, Alberta</p>
    <div class="band-emblem"></div>
  </section>

  <section class="card card-back">
    <div class="wordmark wordmark-back"><span class="mark-square"></span>brovix</div>
    <p class="back-url">www.brovix.example</p>
  </section>
</body>
</html>
```